Create a PPTX template for our business

We need a Powerpoint and Keynote template design for a new company called "Quorvell" We connect hotel guests to hotel employees through text messaging so guests can ask for what they need during their stay. The name "Quorvell" is derived from the word "Affinity" which is how we want our hotel customer's employees and their guests to feel about each other. The color palette chosen is meant to evoke feelings of "warmth" and "comfort," which is how most people feel when they have a strong affinity to each other. The "-ium" ending of Quorvell is intended to give a technological feel to our business since we use technology to connect people together.

A *.ai file is included which contains our logo.

```html
<!DOCTYPE html>
<html lang="en">
<head>
<meta charset="utf-8">
<title>Quorvell Presentation Template</title>
<link href="https://fonts.googleapis.com/css2?family=PT+Sans:ital,wght@0,400;0,700;1,400&family=PT+Sans+Narrow:wght@400;700&display=swap" rel="stylesheet">
<style>
  :root{
    --stage:#1e2325;
    --paper-top:#f7f7f7;
    --paper-bottom:#e6e6e6;
    --teal:#14857e;
    --teal-dark:#0c625d;
    --teal-light:#23a69d;
    --yellow:#d9df2c;
    --ring-teal:#3fb7c2;
    --ink:#2f3a3a;
    --brand-grey:#5a5a5a;
  }
  *{box-sizing:border-box;margin:0;padding:0}
  html,body{width:1200px;height:1000px;overflow:hidden}
  body{background:var(--stage);font-family:"PT Sans Narrow",sans-serif;position:relative}

  .slide{position:absolute;width:588px;height:442px;overflow:hidden;
    background:linear-gradient(180deg,var(--paper-top),var(--paper-bottom));
    box-shadow:0 2px 10px rgba(0,0,0,.6)}
  .slide--cover{left:8px;top:54px}
  .slide--blank{left:604px;top:54px}
  .slide--about{left:8px;top:504px}
  .slide--network{left:604px;top:504px}

  .footer-rule{position:absolute;left:0;right:0;top:394px;height:3px;background:var(--yellow)}
  .footer{position:absolute;left:0;right:0;top:400px;height:42px;
    background:linear-gradient(180deg,var(--teal-light),var(--teal) 55%,var(--teal-dark));}
  .footer__caption{position:absolute;left:20px;top:11px;color:#fff;font-family:"PT Sans",sans-serif;font-style:italic;font-size:14px}
  .slide--cover .footer__caption{left:53px}
  .nav-btn{position:absolute;top:9px;height:26px;width:50px;color:#fff;font-family:"PT Sans",sans-serif;font-size:13px;
    display:flex;align-items:center;justify-content:center;
    background:linear-gradient(180deg,#17776f,#0a514d);
    clip-path:polygon(8px 0,calc(100% - 8px) 0,100% 50%,calc(100% - 8px) 100%,8px 100%,0 50%)}
  .nav-btn--start{left:524px;width:48px}
  .nav-btn--back{left:468px}
  .nav-btn--next{left:524px}

  .brand{position:absolute;display:flex;align-items:center;gap:8px;white-space:nowrap}
  .brand__mark{width:30px;height:30px;background:var(--teal-light);flex:none}
  .brand__name{font-family:"PT Sans",sans-serif;font-weight:400;color:var(--brand-grey);font-size:26px;letter-spacing:0;line-height:1}
  .slide--cover .brand{right:28px;top:314px;gap:10px}
  .slide--cover .brand__mark{width:38px;height:38px}
  .slide--cover .brand__name{font-size:36px;letter-spacing:1px}
  .slide .brand--corner{right:12px;top:352px}

  /* cover */
  .cover__band{position:absolute;left:0;top:0;width:100%;height:258px;
    background:linear-gradient(160deg,#2e2e2e 0%,#4a4a4a 55%,#8a8a8a 100%)}
  .cover__rule{position:absolute;left:0;top:258px;width:100%;height:4px;background:var(--yellow)}
  .cover__title{position:absolute;right:35px;top:96px;color:#fff;font-weight:700;font-size:33px;text-align:right}
  .cover__sub{position:absolute;right:35px;top:142px;color:#f0f0f0;font-family:"PT Sans",sans-serif;font-size:13px;line-height:20px;text-align:right}
  .cover__portrait{position:absolute;left:17px;top:154px;width:216px;height:216px;border-radius:50%;
    border:7px solid var(--yellow);padding:5px;background:#fff}
  .cover__portrait-fill{width:100%;height:100%;border-radius:50%;border:3px solid var(--ring-teal);
    background:radial-gradient(circle at 50% 40%,#e9d6c8,#c9a892 45%,#3b3d44 80%)}

  /* content slides */
  .slide-title{position:absolute;left:0;top:12px;display:flex;align-items:center}
  .slide-title__flag{width:22px;height:30px;margin-right:6px}
  .slide-title__text{color:var(--teal);font-weight:700;font-size:26px}
  .section-heading{position:absolute;top:71px;left:44px;color:var(--teal-dark);font-weight:700;font-size:18px}
  .checklist{position:absolute;top:101px;left:44px;list-style:none;color:var(--ink);font-size:13px;line-height:19px}
  .slide--about .checklist{width:450px}
  .checklist li{position:relative;padding-left:22px}
  .checklist svg{position:absolute;left:0;top:2px;width:15px;height:15px}
  .crowd{position:absolute;left:212px;top:95px;width:345px;height:282px;
    background:linear-gradient(180deg,#c9cdd2 0%,#5a6068 35%,#3c4048 65%,rgba(230,230,230,0) 100%);
    border-radius:6px}
</style>
</head>
<body>
<svg width="0" height="0" style="position:absolute">
  <defs>
    <symbol id="tick" viewBox="0 0 15 15">
      <rect x="1" y="3" width="11" height="11" fill="none" stroke="#1f6f6a" stroke-width="1.5"/>
      <path d="M3.5 8 L6.5 11 L14 1.5" fill="none" stroke="#1f6f6a" stroke-width="2"/>
    </symbol>
    <symbol id="flag" viewBox="0 0 22 30">
      <polygon points="0,0 22,0 22,30 0,30 9,15" fill="#14857e"/>
    </symbol>
  </defs>
</svg>

<section class="slide slide--cover">
  <div class="cover__band"></div>
  <div class="cover__rule"></div>
  <h1 class="cover__title">Project Title Here</h1>
  <p class="cover__sub">Subtext here Subtext here Subtext here Subtext here<br>Subtext here Subtext here Subtext here</p>
  <div class="cover__portrait"><div class="cover__portrait-fill" role="img" aria-label="Presenter portrait photo"></div></div>
  <div class="brand"><span class="brand__mark"></span><span class="brand__name">QUORVELL</span></div>
  <div class="footer-rule"></div>
  <footer class="footer"><span class="footer__caption">Wednesday, 4 February 2015</span><span class="nav-btn nav-btn--start">Start</span></footer>
</section>

<section class="slide slide--blank">
  <div class="slide-title"><svg class="slide-title__flag"><use href="#flag"/></svg><h2 class="slide-title__text">Slide Title Presentation</h2></div>
  <div class="brand brand--corner"><span class="brand__mark"></span><span class="brand__name">QUORVELL</span></div>
  <div class="footer-rule"></div>
  <footer class="footer"><span class="footer__caption">Timeline about your Slide Presentation</span><span class="nav-btn nav-btn--back">Back</span><span class="nav-btn nav-btn--next">Next</span></footer>
</section>

<section class="slide slide--about">
  <div class="slide-title"><svg class="slide-title__flag"><use href="#flag"/></svg><h2 class="slide-title__text">Slide Title Presentation</h2></div>
  <h3 class="section-heading">Castell Modern Real Estate</h3>
  <ul class="checklist">
    <li><svg><use href="#tick"/></svg>High volume local boutique real estate company</li>
    <li><svg><use href="#tick"/></svg>Specialize in selling homes throughout the San Francisco Bay Area</li>
    <li><svg><use href="#tick"/></svg>Focus on modern marketing techniques and thinking outside the box</li>
    <li><svg><use href="#tick"/></svg>“High Tech and High Touch” approach to real estate</li>
    <li><svg><use href="#tick"/></svg>Certified Green Business Everything is done and stored online. No File Cabinets in our offices!</li>
    <li><svg><use href="#tick"/></svg>Exceptional web presence far beyond other local real estate companies</li>
    <li><svg><use href="#tick"/></svg>Clean, streamline, and hip marketing materials</li>
    <li><svg><use href="#tick"/></svg>A company constantly looking into the latest real estate trends, tools, and technology to better assist their agents and clients sell homes in the modern world, all while embracing tried and true real estate values and practices as well</li>
    <li><svg><use href="#tick"/></svg>Leading authority for architectural homes and recognized world wide</li>
    <li><svg><use href="#tick"/></svg>Not Just Modern Homes! We focus on Modern Real Estate<br>Practices through and through.</li>
  </ul>
  <div class="brand brand--corner"><span class="brand__mark"></span><span class="brand__name">QUORVELL</span></div>
  <div class="footer-rule"></div>
  <footer class="footer"><span class="footer__caption">Timeline about your Slide Presentation</span><span class="nav-btn nav-btn--back">Back</span><span class="nav-btn nav-btn--next">Next</span></footer>
</section>

<section class="slide slide--network">
  <div class="slide-title"><svg class="slide-title__flag"><use href="#flag"/></svg><h2 class="slide-title__text">Slide Title Presentation</h2></div>
  <h3 class="section-heading">I’ve got connections!</h3>
  <ul class="checklist">
    <li><svg><use href="#tick"/></svg>Handymen</li>
    <li><svg><use href="#tick"/></svg>Contractors</li>
    <li><svg><use href="#tick"/></svg>Stagers</li>
    <li><svg><use href="#tick"/></svg>Painters</li>
    <li><svg><use href="#tick"/></svg>Cleaners</li>
    <li><svg><use href="#tick"/></svg>Movers</li>
    <li><svg><use href="#tick"/></svg>Storage companies</li>
    <li><svg><use href="#tick"/></svg>Landscapers</li>
    <li><svg><use href="#tick"/></svg>Estate Sale Professionals</li>
    <li><svg><use href="#tick"/></svg>Lawyers</li>
    <li><svg><use href="#tick"/></svg>Mortgage Brokers</li>
    <li><svg><use href="#tick"/></svg>Inspectors</li>
  </ul>
  <div class="crowd" role="img" aria-label="Group photo of business professionals and tradespeople standing together"></div>
  <div class="brand brand--corner"><span class="brand__mark"></span><span class="brand__name">QUORVELL</span></div>
  <div class="footer-rule"></div>
  <footer class="footer"><span class="footer__caption">Timeline about your Slide Presentation</span><span class="nav-btn nav-btn--back">Back</span><span class="nav-btn nav-btn--next">Next</span></footer>
</section>
</body>
</html>
```